Quillmarsh Property Solutions need a business card design

Hello guys. We would need a business card design asap please.
We are a start up property investment business based in London UK specialised in buying, selling, managing and letting properties and helping distressed property owners.
The name of our Business is Quillmarsh, the logo symbolises the four fundamental elements of the world (earth, air, fire and water) and so it stands for strength, stability, longevity.
We would like the business card to communicate professionalism and reliability. Many many thanks indeed for your work.

Details:

1.) Rosalind Updike
Property Investor
Mobile: +44(0)7700123456
Email: rosalind.quillmarsh@mailbox-example.com

2.) Dominic Updike
Property Investor
Mobile: +44(0)7700987654
Email: dominic.quillmarsh@mailbox-example.com

```html
<!DOCTYPE html>
<html lang="en">
<head>
<meta charset="utf-8">
<title>Quillmarsh Property Solutions – Business Card</title>
<link rel="stylesheet" href="https://fonts.googleapis.com/css2?family=Open+Sans:wght@400;600;700&display=swap">
<style>
  :root {
    --page-bg: #e6e6ec;
    --card-white: #ffffff;
    --brand-blue: #2f6fd6;
    --brand-blue-light: #5b95ea;
    --brand-blue-deep: #1d5bc9;
    --brand-green: #22b24c;
    --name-blue: #1f5fcf;
    --text-grey: #555a60;
    --logo-grey: #8a8d91;
    --logo-dark: #1b1b1b;
    --contact-white: #ffffff;
  }
  * { box-sizing: border-box; margin: 0; padding: 0; }
  html, body { width: 1200px; height: 987px; overflow: hidden; }
  body {
    background: var(--page-bg);
    font-family: "Open Sans", sans-serif;
    position: relative;
  }
  .card {
    position: absolute;
    width: 700px;
    height: 400px;
    border-radius: 34px;
    background: var(--card-white);
    overflow: hidden;
    box-shadow: 0 10px 30px rgba(0,0,0,0.12);
  }
  .card--back { left: 440px; top: 50px; }
  .card--front { left: 60px; top: 530px; }

  /* Back card */
  .back-brand {
    position: absolute;
    left: 0; right: 0; top: 100px;
    text-align: center;
  }
  .brand-mark {
    display: inline-block;
    width: 56px; height: 56px;
    background: var(--logo-dark);
    margin-bottom: 16px;
  }
  .brand-name {
    font-weight: 700;
    font-size: 38px;
    line-height: 1.1;
    letter-spacing: 1px;
    text-transform: uppercase;
    color: var(--logo-dark);
  }
  .brand-sub {
    font-weight: 700;
    font-size: 17px;
    letter-spacing: 1px;
    text-transform: uppercase;
    color: var(--logo-dark);
  }
  .back-web {
    position: absolute;
    left: 0; right: 0; top: 290px;
    text-align: center;
    font-size: 22px;
    letter-spacing: 3px;
    color: var(--text-grey);
  }

  /* Front card */
  .front-swoosh { position: absolute; inset: 0; width: 700px; height: 400px; }
  .front-brand {
    position: absolute;
    left: 48px; top: 36px;
  }
  .front-brand .brand-mark {
    background: var(--logo-grey);
    width: 50px; height: 50px;
    margin-bottom: 10px;
  }
  .front-brand .brand-name,
  .front-brand .brand-sub { color: var(--logo-grey); }
  .front-brand .brand-name { font-size: 30px; }
  .front-brand .brand-sub { font-size: 15px; }
  .holder {
    position: absolute;
    right: 48px; top: 96px;
    text-align: left;
  }
  .holder-name {
    font-weight: 600;
    font-size: 28px;
    line-height: 1.2;
    color: var(--name-blue);
  }
  .holder-role {
    font-size: 19px;
    color: var(--text-grey);
  }
  .contacts {
    position: absolute;
    right: 36px; bottom: 24px;
    list-style: none;
    color: var(--contact-white);
    font-size: 18px;
    line-height: 1.8;
  }
  .contacts li { display: flex; align-items: center; justify-content: flex-end; gap: 10px; }
  .contacts svg { width: 18px; height: 18px; flex: none; }
</style>
</head>
<body>

  <section class="card card--back" aria-label="Card back">
    <div class="back-brand">
      <span class="brand-mark"></span>
      <p class="brand-name">Quillmarsh</p>
      <p class="brand-sub">Property Solutions</p>
    </div>
    <p class="back-web">www.quillmarsh-example.com</p>
  </section>

  <section class="card card--front" aria-label="Card front">
    <svg class="front-swoosh" viewBox="0 0 700 400" aria-hidden="true">
      <defs>
        <linearGradient id="blueBand" x1="0" y1="0" x2="1" y2="1">
          <stop offset="0" stop-color="#5b95ea"/>
          <stop offset="1" stop-color="#1d5bc9"/>
        </linearGradient>
      </defs>
      <path d="M0,196 C110,290 300,316 470,312 C300,322 110,300 0,226 Z" fill="var(--brand-green)"/>
      <path d="M0,240 C120,320 330,336 440,326 C560,314 650,210 700,150 L700,400 L0,400 Z" fill="url(#blueBand)"/>
    </svg>

    <div class="front-brand">
      <span class="brand-mark"></span>
      <p class="brand-name">Quillmarsh</p>
      <p class="brand-sub">Property Solutions</p>
    </div>

    <div class="holder">
      <p class="holder-name">Rosalind Updike</p>
      <p class="holder-role">Property Investor</p>
    </div>

    <ul class="contacts">
      <li>
        <svg viewBox="0 0 24 24" aria-hidden="true"><rect x="6" y="2" width="12" height="20" rx="2" fill="none" stroke="currentColor" stroke-width="2"/><circle cx="12" cy="18" r="1.3" fill="currentColor"/></svg>
        +44(0)7700123456
      </li>
      <li>
        <svg viewBox="0 0 24 24" aria-hidden="true"><rect x="2" y="5" width="20" height="14" rx="2" fill="currentColor"/><path d="M3 6 L12 13 L21 6" fill="none" stroke="#2f6fd6" stroke-width="2"/></svg>
        rosalind.quillmarsh@mailbox-example.com
      </li>
    </ul>
  </section>

</body>
</html>
```